Flyer Design Project for Sports Medicine Services

I am a sports medicine doctor specialising in the diagnosis and management of sport and exercise injuries for all ages and levels of activity - from elite to weekend jogger. I work under the Business name Peak Stride Athletics and do have a company logo. I am wanting a flier that I can send to family doctors, physiotherapists and sports clubs explaining who I am what I can offer and why they should send me patients.
- I have a Masters in Sports Medicine (MSportsMed), Diplomas in Obstetrics/Gynaecology (DRANZCOG) and also Paediatrics (DCH) and certificate in advanced clinical hypnosis
-accurate diagnosis and management plan with their regular physio to return the player / athlete to the field / court /gym as soon as safely possible
-hypnosis for sports performance eg anxiety control, confidence and mental rehearsal for individuals and teams
- because there are many possible therapists and therapy options, as a sports doctor I can work out who they need to see a physiotherapist, surgeon, massage therapist chiropractor or podiatrist to return them to activity or whether cortisone, PRP or autologous blood injections are needed
-can provide one point of contact for coaches and clubs for rehabilitation and return to sport advice.
- work with Simon Drewett ex Australian Athlete, a Performance Strategist (NLB listed resource person) and registered Psychologist for best mental preparation for individuals teams and coach development
- can organise rapid access to MRI, ultrasound and specialist appointments if needed
-I work at 3 practices KinetaCare 518 Hollis Rd Hollis 84619027 Monday Wednesday Friday; Brackley Sports Clinic, 193 Brackley Rd, Adelaide 81946372 Tuesday Riverton Hawks Sports Medicine Clinic, Tolvane Arena 8162 5907 Thursday.
-facebook site peakstrideathletics
Updates
Hi All, just to clarify.. My name is Simon Drewett and I am the sports doctor. My wife is Simon Drewett and she is the psychologist. The flier should mainly be advertising my sports medicine services and a byline ( or at least not the first line in the title) about the Performance Strategy and Coach development.
Target Market(s)
family doctors (GPs), Sporting Clubs, Physiotherapists
Industry/Entity Type
Massage
Look and feel

```html
<!DOCTYPE html>
<html lang="en">
<head>
<meta charset="utf-8">
<title>Peak Stride Athletics – Sports Medicine Flyer</title>
<link href="https://fonts.googleapis.com/css2?family=Arimo:wght@400;700&family=Roboto+Condensed:wght@400&display=swap" rel="stylesheet">
<style>
  :root {
    --page-bg: #ece9e4;
    --ink-black: #111111;
    --brand-blue: #2ba8e0;
    --brand-green: #b6d335;
    --white: #ffffff;
    --text-dark: #1a1a1a;
  }
  * { margin: 0; padding: 0; box-sizing: border-box; }
  html, body { width: 891px; height: 1200px; overflow: hidden; background: var(--page-bg); }
  .flyer {
    position: absolute; left: 49px; top: 40px;
    width: 793px; height: 1120px;
    background: var(--white);
    overflow: hidden;
    font-family: "Arimo", Arial, sans-serif;
    color: var(--text-dark);
  }
  .photo { position: absolute; }
  .photo-consult {
    left: 240px; top: 0; width: 553px; height: 500px;
    background: linear-gradient(120deg, #e9e4dc 0%, #d9d2c6 35%, #cfd8dc 60%, #eef0ee 100%);
  }
  .photo-lawn {
    left: 0; top: 250px; width: 280px; height: 200px;
    background: linear-gradient(160deg, #8fae4c 0%, #6f9336 55%, #587b2a 100%);
  }
  .shapes { position: absolute; left: 0; top: 0; width: 793px; height: 1120px; }
  .brand-name {
    position: absolute; left: 28px; top: 134px;
    font-weight: 700;
    font-size: 27px; line-height: 30px; letter-spacing: -0.5px;
    color: var(--brand-blue);
  }
  .headline {
    position: absolute; left: 40px; right: 75px; top: 468px;
    text-align: right;
    font-family: "Roboto Condensed", "Arial Narrow", sans-serif; font-weight: 400;
    font-size: 54px; line-height: 60px; color: var(--white);
  }
  .intro {
    position: absolute; left: 72px; right: 80px; top: 622px;
    font-size: 19.5px; line-height: 25px; color: var(--text-dark);
  }
  .services { position: absolute; left: 72px; right: 75px; top: 738px; list-style: none; }
  .services li {
    position: relative; padding-left: 30px;
    font-size: 17.3px; line-height: 22px; margin-bottom: 23px;
  }
  .services li.justified { text-align: justify; }
  .services svg { position: absolute; left: 0; top: 2px; width: 22px; height: 18px; }
  .locations { position: absolute; left: 0; top: 1008px; width: 793px; color: var(--white); font-size: 15.4px; line-height: 19.5px; }
  .location { position: absolute; top: 0; }
  .location.mwf { left: 35px; }
  .location.tue { left: 268px; }
  .location.thu { left: 499px; }
</style>
</head>
<body>
<main class="flyer">
  <div class="photo photo-consult" role="img" aria-label="Photo of a doctor examining a young boy's knee while the boy holds a football"></div>
  <div class="photo photo-lawn" role="img" aria-label="Photo of a boy in football gear lying on a grass field"></div>

  <svg class="shapes" viewBox="0 0 661 933" preserveAspectRatio="none" aria-hidden="true">
    <path d="M0 0 H252 C266 70 255 155 205 196 C160 230 70 236 0 228 Z" fill="var(--ink-black)" stroke="var(--white)" stroke-width="7"/>
    <path d="M0 352 C200 288 450 290 661 385 V933 H0 Z" fill="var(--white)"/>
    <path d="M0 360 C100 330 200 318 300 316 L300 933 H0 Z" fill="var(--brand-blue)"/>
    <path d="M0 490 C40 400 150 330 330 318 C480 310 600 350 661 392 V933 H0 Z" fill="var(--brand-green)"/>
    <rect x="0" y="805" width="661" height="128" fill="var(--white)"/>
    <rect x="0" y="811" width="661" height="122" fill="var(--brand-blue)"/>
    <line x1="206" y1="833" x2="206" y2="900" stroke="var(--white)" stroke-width="1"/>
    <line x1="402" y1="833" x2="402" y2="900" stroke="var(--white)" stroke-width="1"/>
  </svg>

  <div class="brand-name">Peak Stride<br>Athletics</div>

  <h1 class="headline">Expert Sports Medicine Care &amp;<br>High Performance Psychology</h1>

  <p class="intro">Simon Drewett a sports medicine doctor specialising in the diagnosis and management of sport and exercise injuries for all ages and levels of activity - from elite to weekend jogger.</p>

  <ul class="services">
    <li class="justified">
      <svg viewBox="0 0 22 18"><rect x="1" y="3" width="14" height="14" fill="none" stroke="#111" stroke-width="1.6"/><path d="M4 9 L8 13 L20 1" fill="none" stroke="#111" stroke-width="3"/></svg>
      I have a Masters in Sports Medicine (MSportsMed), Diplomas in Obstetrics/Gynaecology (DRANZCOG) and also Paediatrics (DCH) and certificate in advanced clinical hypnosis
    </li>
    <li>
      <svg viewBox="0 0 22 18"><rect x="1" y="3" width="14" height="14" fill="none" stroke="#111" stroke-width="1.6"/><path d="M4 9 L8 13 L20 1" fill="none" stroke="#111" stroke-width="3"/></svg>
      Accurate diagnosis and management plan with their regular physio to return the player / athlete to the field / court /gym as soon as safely possible
    </li>
    <li>
      <svg viewBox="0 0 22 18"><rect x="1" y="3" width="14" height="14" fill="none" stroke="#111" stroke-width="1.6"/><path d="M4 9 L8 13 L20 1" fill="none" stroke="#111" stroke-width="3"/></svg>
      Hypnosis for sports performance eg anxiety control, confidence and mental rehearsal for individuals and teams
    </li>
  </ul>

  <section class="locations">
    <div class="location mwf">Monday Wednesday Friday<br>KinetaCare<br>518 Hollis Rd Hollis<br>84619027</div>
    <div class="location tue">Tuesday<br>Brackley Sports Clinic<br>193 Brackley Rd, Adelaide<br>81946372</div>
    <div class="location thu">Thursday<br>Riverton Hawks Sports Medicine Clinic<br>Tolvane Arena<br>8162 5907</div>
  </section>
</main>
</body>
</html>
```